Banner ads for LP that work with same theme as below banners

Love the banner ads below. Need more with attached photos. But use the same wording, font as in below banner ads. Should be LP size 1200/627 so I can use for Pixorly and LP. Looking for great ads to use as LP ads. We do lots of ads so it will be worth your time to enter this contest you will be rewarded with a ton of work. Need several banner ads that work together. So maybe 1 of the dresses, 1 of the sweater, 1 of the leggings, 1 of the jacket

Target Market(s)

Women 24-45

Industry/Entity Type

Fashion

Requirements
Must have
• Banner ads that work for LP and Pixorly
Nice to have
• Several options to choose from
Should not have
• not sure

```html
<!DOCTYPE html>
<html lang="en">
<head>
<meta charset="utf-8">
<title>Winter Wear Collection</title>
<link href="https://fonts.googleapis.com/css2?family=Rochester&family=Playfair+Display:wght@400;700;900&display=swap" rel="stylesheet">
<style>
  :root {
    --canvas: #ffffff;
    --panel-top: #c8d3dc;
    --panel-mid: #d2dae1;
    --panel-low: #d6dee5;
    --base-block: #f2f3f4;
    --ink: #33363b;
    --light: #ffffff;
    --jacket: #22406e;
    --jacket-deep: #1b3358;
    --hair: #b98a5c;
    --skin: #dcb59c;
    --fur: #c9bfb4;
    --knit: #a8a8a8;
    --legging: #18181a;
  }
  * { margin: 0; padding: 0; box-sizing: border-box; }
  html, body { width: 1200px; height: 627px; overflow: hidden; background: var(--canvas); }
  .banner { position: relative; width: 1200px; height: 627px; background: var(--canvas); overflow: hidden; }

  .photo-closeup {
    position: absolute; left: 0; top: 0; width: 455px; height: 627px;
    background:
      radial-gradient(ellipse 55% 40% at 25% 22%, rgba(220,181,156,0.9) 0%, rgba(220,181,156,0) 100%),
      radial-gradient(ellipse 50% 60% at 60% 40%, rgba(185,138,92,0.85) 0%, rgba(185,138,92,0) 100%),
      linear-gradient(180deg, #e8d6c8 0%, var(--hair) 40%, var(--jacket) 75%, var(--jacket-deep) 100%);
  }
  .photo-model {
    position: absolute; left: 500px; top: 72px; width: 268px; height: 555px;
    border-radius: 90px 90px 24px 24px;
    background:
      linear-gradient(180deg, var(--hair) 0%, var(--fur) 26%, var(--jacket) 40%, var(--jacket) 76%, var(--knit) 86%, var(--legging) 92%, var(--legging) 100%);
    opacity: 0.92;
  }

  .promo-panel {
    position: absolute; left: 852px; top: 0; width: 277px; height: 540px;
    background: linear-gradient(180deg, var(--panel-top) 0%, var(--panel-mid) 55%, var(--panel-low) 100%);
  }
  .promo-base {
    position: absolute; left: 852px; top: 540px; width: 277px; height: 87px;
    background: var(--base-block);
  }
  .promo-title {
    position: absolute; left: 903px; top: 0; width: 201px; height: 0; text-align: center; font-weight: normal;
  }
  .promo-title .script {
    position: absolute; top: 309px; left: 0; width: 100%;
    font-family: "Rochester", cursive; font-weight: 400; font-size: 34px; color: var(--light);
    letter-spacing: 2px; line-height: 1;
  }
  .promo-title .caps {
    position: absolute; top: 346px; left: 0; width: 100%;
    font-family: "Playfair Display", serif; font-weight: 700; font-size: 20px;
    letter-spacing: 4px; padding-left: 4px; color: var(--ink); line-height: 1;
  }
  .shop-button {
    position: absolute; left: 903px; top: 397px; width: 201px; height: 43px;
    background: var(--light); display: flex; align-items: center; justify-content: center;
    font-family: "Playfair Display", serif; font-size: 12px; letter-spacing: 2.5px;
    color: var(--ink); text-decoration: none;
  }
  .shop-button b { font-weight: 900; }
  .shop-button span { font-weight: 400; margin: 0 5px; }
</style>
</head>
<body>
  <main class="banner">
    <div class="photo-closeup" role="img" aria-label="Close-up of a woman with long wavy hair wearing a navy quilted jacket with a faux fur collar"></div>
    <div class="photo-model" role="img" aria-label="Woman in a navy puffer jacket with faux fur collar and grey knit hem, black leggings"></div>

    <div class="promo-panel"></div>
    <div class="promo-base"></div>
    <h1 class="promo-title">
      <span class="script">Winter Wear</span>
      <span class="caps">COLLECTION</span>
    </h1>
    <a class="shop-button" href="#"><b>SHOP</b><span>THE</span><b>SEASON</b></a>
  </main>
</body>
</html>
```